BOLD & MINIMALIST DESIGN NEEDED

We want a very bold but minimalistic business card design that is impactful and utilizes both sides of the business card. Our current logo is included for your use.

We want bold fonts and good use of negative space. We don't want the logo to overpower the design.

Target Market(s)

Professionals who are building new commercial buildings.

Industry/Entity Type

Construction

Contact Information for Business Card

Name, Title, email, office phone, cell phone, website

Font styles to use
Serif
Sans Serif

Requirements
Must have
• Bold design!

```html
<!DOCTYPE html>
<html lang="en">
<head>
<meta charset="UTF-8">
<title>Summitline Design + Build — Business Card</title>
<link href="https://fonts.googleapis.com/css2?family=Montserrat:wght@300;500;600;700;900&display=swap" rel="stylesheet">
<style>
  :root {
    --stage: #a1a1a1;
    --ink: #111111;
    --card-dark: #1a1a1a;
    --card-light: #ffffff;
    --brand-green: #7cc242;
    --ghost: #ececee;
    --ghost-green: #f3f8ef;
    --white: #ffffff;
  }
  * { margin: 0; padding: 0; box-sizing: border-box; }
  html, body {
    width: 1200px; height: 1009px; overflow: hidden;
    background: var(--stage);
    font-family: "Montserrat", sans-serif;
  }
  .canvas { position: relative; width: 1200px; height: 1009px; }
  .card {
    position: absolute; left: 220px; width: 760px; height: 434px;
    overflow: hidden;
    box-shadow: 0 10px 24px rgba(0,0,0,0.28);
  }

  /* Back side */
  .card--back { top: 50px; background: var(--card-dark); }
  .card--back .brand {
    position: absolute; left: 0; right: 0; top: 150px;
    display: flex; flex-direction: column; align-items: center;
  }
  .card--back .brand-row { display: flex; align-items: center; gap: 20px; }
  .card--back .brand-mark { width: 44px; height: 44px; background: var(--brand-green); }
  .card--back .brand-name {
    color: var(--white); font-weight: 900; font-size: 78px; letter-spacing: 1px; line-height: 1;
  }
  .card--back .brand-rule { width: 470px; height: 2px; background: var(--white); margin-top: 14px; }
  .card--back .brand-tagline {
    color: var(--white); font-weight: 300; font-size: 22px; letter-spacing: 12px; margin-top: 10px;
  }

  /* Front side */
  .card--front { top: 525px; background: var(--card-light); }
  .card--front .ghost-panel {
    position: absolute; right: 0; top: 0; width: 300px; height: 100%;
    background: linear-gradient(160deg, var(--ghost-green), var(--ghost));
  }
  .card--front .brand { position: absolute; left: 54px; top: 52px; }
  .card--front .brand-name {
    color: var(--ink); font-weight: 900; font-size: 46px; line-height: 1; letter-spacing: 0.5px;
  }
  .card--front .brand-rule { width: 300px; height: 2px; background: var(--ink); margin-top: 6px; }
  .card--front .brand-tagline {
    color: var(--ink); font-weight: 500; font-size: 14px; letter-spacing: 8px; margin-top: 4px; padding-left: 40px;
  }
  .accent-bar {
    position: absolute; left: 30px; top: 176px; width: 10px; height: 62px; background: var(--brand-green);
  }
  .person { position: absolute; left: 54px; top: 172px; }
  .person-name { font-weight: 700; font-size: 34px; color: var(--ink); line-height: 1.1; }
  .person-title { font-weight: 600; font-size: 21px; color: var(--ink); margin-top: 4px; }
  .contacts { position: absolute; left: 60px; top: 262px; list-style: none; }
  .contact {
    display: flex; align-items: center; gap: 14px;
    font-weight: 600; font-size: 22px; color: var(--ink); height: 34px;
  }
  .contact svg { width: 22px; height: 22px; fill: var(--brand-green); flex: none; }
</style>
</head>
<body>
<main class="canvas">

  <section class="card card--back" aria-label="Card back">
    <div class="brand">
      <div class="brand-row">
        <span class="brand-mark"></span>
        <span class="brand-name">SUMMITLINE</span>
      </div>
      <div class="brand-rule"></div>
      <div class="brand-tagline">DESIGN + BUILD</div>
    </div>
  </section>

  <section class="card card--front" aria-label="Card front">
    <div class="ghost-panel"></div>

    <div class="brand">
      <div class="brand-name">SUMMITLINE</div>
      <div class="brand-rule"></div>
      <div class="brand-tagline">DESIGN + BUILD</div>
    </div>

    <div class="accent-bar"></div>
    <div class="person">
      <div class="person-name">Marcus Delaney</div>
      <div class="person-title">Founder &amp; CEO</div>
    </div>

    <ul class="contacts">
      <li class="contact">
        <svg viewBox="0 0 24 24" aria-hidden="true"><path d="M3 9c0-3 4-5 9-5s9 2 9 5v2h-5V9H8v2H3zM6 12h12l2 8H4z"/></svg>
        555-014-2200
      </li>
      <li class="contact">
        <svg viewBox="0 0 24 24" aria-hidden="true"><path d="M7 1h10a2 2 0 0 1 2 2v18a2 2 0 0 1-2 2H7a2 2 0 0 1-2-2V3a2 2 0 0 1 2-2zm0 3v15h10V4zm5 16a1 1 0 1 0 0 2 1 1 0 0 0 0-2z"/></svg>
        555-014-2201
      </li>
      <li class="contact">
        <svg viewBox="0 0 24 24" aria-hidden="true"><path d="M2 5h20v14H2zm2 2v.5l8 5.5 8-5.5V7zm0 3v7h16v-7l-8 5.5z"/></svg>
        info@summitline-db.com
      </li>
      <li class="contact">
        <svg viewBox="0 0 24 24" aria-hidden="true"><circle cx="12" cy="12" r="10"/><path d="M7 8c2 0 3 1 3 3s-2 2-2 4-2 1-3-1zM14 5c2 1 4 2 4 5-1 0-3-1-4 0s1 3-1 4-1-4-2-5 1-3 3-4z" fill="#ffffff"/></svg>
        www.summitline-db.com
      </li>
    </ul>
  </section>

</main>
</body>
</html>
```